New Business Card for Web Design/Internet Marketing Company

Looking for a great looking new business card. We are a 10 year old web design, internet marketing and website management company that works mostly with small businesses.

Our new card needs to better match the colors and style of our website, be bold, extremely usable and slightly edgy.

Target Market(s)

Small/Medium businesses that have websites

Industry/Entity Type

Internet

Requirements
Must have
• Front and back design, full color, rounded corners please

Must use the colors/style of our website (JPG provided)

INFO FOR CARDS (as readable as possible please)
Mark Lenner
President/CEO
mark@trelvanmedia.example
Phone: 520-381-7459
Toll Free: 866-381-7459
Address: 4315 W. Calloway Ave. Ste. 140, Tucson, AZ 85792

THINGS I WANT TO PROMOTE (if there is room):
1. Our Website - www.trelvanmedia.example

2. Social Media
Twitter: @trelvanmedia
Facebook: www.facebook.com/trelvanmedia

3. Our Services
Web Design
Internet Marketing
Website Management

```html
<!DOCTYPE html>
<html lang="en">
<head>
<meta charset="utf-8">
<title>Trelvan Media – Business Card</title>
<link rel="stylesheet" href="https://fonts.googleapis.com/css2?family=Open+Sans:wght@400;600;700&display=swap">
<style>
  :root {
    --brand-blue: #1b8fcd;
    --brand-blue-deep: #137fbb;
    --brand-orange: #f08a2c;
    --paper: #ffffff;
    --ink: #3c3c3c;
    --backdrop: #e8e4df;
  }
  * { margin: 0; padding: 0; box-sizing: border-box; }
  html, body {
    width: 1200px; height: 402px; overflow: hidden;
    background: var(--backdrop);
    font-family: "Open Sans", Arial, sans-serif;
  }
  .sheet { position: relative; width: 1200px; height: 402px; }

  .card {
    position: absolute; top: 58px;
    width: 543px; height: 293px;
    border-radius: 8px; overflow: hidden;
  }
  .card--front { left: 63px; background: var(--paper); }
  .card--back { left: 626px; background: var(--brand-blue); color: #fff; text-align: center; }

  .card__shape { position: absolute; inset: 0; }

  .holder {
    position: absolute; top: 6px; left: 0; width: 100%;
    text-align: center; color: var(--brand-blue);
    font-weight: 700; font-size: 17px;
  }
  .holder__title { font-weight: 400; font-size: 12px; }

  .wordmark {
    position: absolute; left: 0; width: 100%;
    display: flex; align-items: center; justify-content: center; gap: 12px;
    font-weight: 700; letter-spacing: -0.5px;
  }
  .wordmark__dot { width: 26px; height: 26px; border-radius: 50%; background: var(--brand-orange); }
  .card--front .wordmark { top: 86px; font-size: 40px; color: var(--brand-blue); }
  .card--back .wordmark { top: 70px; font-size: 40px; color: #fff; }
  .card--back .wordmark__dot { background: #fff; }

  .address {
    position: absolute; top: 184px; left: 0; width: 100%;
    text-align: center; font-size: 12px; color: var(--ink);
  }

  .contacts {
    position: absolute; top: 247px; left: 0; width: 100%;
    display: flex; justify-content: center; color: #fff; font-size: 12.5px;
  }
  .contacts__col { padding: 0 10px; line-height: 19px; }
  .contacts__col + .contacts__col { border-left: 1px solid rgba(255,255,255,.85); }
  .contacts__item { display: flex; align-items: center; gap: 5px; }
  .contacts__item svg { width: 9px; height: 9px; flex: none; }

  .services__heading {
    position: absolute; top: 152px; left: 0; width: 100%;
    font-size: 21px; font-weight: 600;
  }
  .services__rule {
    position: absolute; top: 183px; left: 177px; width: 172px;
    height: 2px; background: #fff;
  }
  .services__list {
    position: absolute; top: 199px; left: 0; width: 100%;
    font-size: 18px; line-height: 25px;
  }
  .social {
    position: absolute; top: 266px; left: 0; width: 100%;
    display: flex; justify-content: center; gap: 46px;
    font-size: 12.5px;
  }
</style>
</head>
<body>
<main class="sheet">

  <section class="card card--front" aria-label="Card front">
    <svg class="card__shape" viewBox="0 0 543 293" preserveAspectRatio="none" aria-hidden="true">
      <path d="M0,180 Q260,290 543,190 L543,293 L0,293 Z" fill="var(--brand-orange)"/>
      <path d="M0,190 Q260,296 543,193 L543,293 L0,293 Z" fill="var(--brand-blue)"/>
    </svg>

    <p class="holder">Mark Lenner, <span class="holder__title">President/CEO</span></p>

    <div class="wordmark"><span class="wordmark__dot"></span><span>Trelvan Media</span></div>

    <p class="address">4315 W. Calloway Ave. Ste. 140, Tucson, AZ 85792</p>

    <div class="contacts">
      <div class="contacts__col">
        <p class="contacts__item">
          <svg viewBox="0 0 10 10"><circle cx="5" cy="5" r="4.5" fill="none" stroke="#fff"/><path d="M3.2 2.8l1 1-.6.6a3 3 0 0 0 2 2l.6-.6 1 1-.8.8C4.5 7.4 2.6 5.5 2.4 3.6z" fill="#fff"/></svg>
          520-381-7459
        </p>
        <p class="contacts__item">
          <svg viewBox="0 0 10 10"><circle cx="5" cy="5" r="4.5" fill="none" stroke="#fff"/><path d="M3.2 2.8l1 1-.6.6a3 3 0 0 0 2 2l.6-.6 1 1-.8.8C4.5 7.4 2.6 5.5 2.4 3.6z" fill="#fff"/></svg>
          866-381-7459
        </p>
      </div>
      <div class="contacts__col">
        <p class="contacts__item">
          <svg viewBox="0 0 10 10"><rect x="0.5" y="2" width="9" height="6" fill="#fff"/><path d="M0.5 2l4.5 3.5L9.5 2" fill="none" stroke="var(--brand-blue)" stroke-width=".8"/></svg>
          mark@trelvanmedia.example
        </p>
        <p class="contacts__item">
          <svg viewBox="0 0 10 10"><circle cx="5" cy="5" r="4.3" fill="none" stroke="#fff"/><ellipse cx="5" cy="5" rx="1.8" ry="4.3" fill="none" stroke="#fff" stroke-width=".8"/><path d="M0.7 5h8.6" stroke="#fff" stroke-width=".8"/></svg>
          www.trelvanmedia.example
        </p>
      </div>
    </div>
  </section>

  <section class="card card--back" aria-label="Card back">
    <div class="wordmark"><span class="wordmark__dot"></span><span>Trelvan Media</span></div>

    <h2 class="services__heading">Our Services</h2>
    <div class="services__rule"></div>
    <p class="services__list">Web Design &bull; Internet Marketing<br>Website Management</p>

    <div class="social">
      <span>@trelvanmedia</span>
      <span>trelvanmedia</span>
    </div>
  </section>

</main>
</body>
</html>
```